New Wix logo and website layout

I need a new logo design and a new, modern website layout design. I am a professional therapist providing remedial massage. I am Canadian but live in Australia & would like the logo to have a somewhat 'Canadian feel' to it (something subtle i.e. no flags) I currently have a maple tree leaf as my logo. my current website is tidewaterbodywork.com.au. I need the website to work on mobile phones & traditional web browsers.

Target Market(s)

customers looking for remedial massage and manual lymphatic drainage

Industry/Entity Type

professional massage

Coding

Coded - Design and coding required

Font styles to use
Sans Serif

Colors
EB3D1F
EC4F4E
F09395
F8D3D4
FCEDEE

Requirements
Nice to have
• something subtle that indicates that I am canadian
Should not have
• no flags. nothing too bold

```html
<!DOCTYPE html>
<html lang="en">
<head>
<meta charset="utf-8">
<title>Tidewater Bodywork – Hours</title>
<link href="https://fonts.googleapis.com/css2?family=Libre+Baskerville:wght@700&family=Poppins:wght@400;500;600&display=swap" rel="stylesheet">
<style>
:root{
  --red:#EB3D1F;
  --coral:#EC4F4E;
  --pink:#F09395;
  --blush:#F8D3D4;
  --mist:#FCEDEE;
  --ink:#2a2a2a;
  --white:#fff;
}
*{box-sizing:border-box;margin:0;padding:0}
html,body{width:722px;height:1200px;overflow:hidden;background:var(--white)}
body{position:relative;font-family:'Poppins',sans-serif;color:var(--ink)}
.serif{font-family:'Libre Baskerville',serif;font-weight:700}
.abs{position:absolute}

.topbar{left:0;top:0;width:722px;height:32px;background:var(--coral);color:var(--white);font-size:11px}
.topbar .social{left:44px;top:10px;display:flex;gap:14px}
.dot{width:12px;height:12px;border-radius:50%;background:var(--white);display:block}
.topbar .contact{right:44px;top:8px;display:flex;gap:14px;align-items:center}
.topbar .contact span{display:flex;align-items:center;gap:6px}

.header{left:0;top:32px;width:722px;height:62px}
.brand{left:44px;top:11px;display:flex;align-items:center;gap:9px}
.brand-mark{width:38px;height:38px;border:2px solid var(--red);border-radius:50%}
.brand-name{font-size:17px;line-height:20px;color:var(--ink);letter-spacing:.5px}
.nav{right:44px;top:26px;display:flex;gap:22px;font-size:9px;letter-spacing:.4px}
.nav .active{color:var(--coral)}

.hero{left:0;top:94px;width:722px;height:215px;background:linear-gradient(100deg,#c8a88a 0%,#b9835f 45%,#8f5f45 75%,#5b4a40 100%)}
.hero h1{position:absolute;left:45px;top:86px;font-size:39px;color:var(--white);letter-spacing:1px}

.hex{left:46px;top:400px;width:255px;height:294px}
.hours{left:370px;top:396px;width:310px}
.hours h2{font-size:22px;color:var(--red);letter-spacing:.5px}
.hours p{font-size:8.6px;line-height:19px;margin-top:10px}
.hours table{margin-top:12px;border-collapse:collapse;font-family:'Libre Baskerville',serif;font-weight:700;font-size:9.5px;letter-spacing:.4px}
.hours td{height:30px;padding:0}
.hours td:first-child{width:141px}
.closed{color:var(--red)}

.contact-band{left:0;top:751px;width:722px;height:354px;background:linear-gradient(120deg,#c82d1a 0%,#d9371e 40%,#c42c18 70%,#b3261a 100%);color:var(--white)}
.contact-band h2{position:absolute;font-size:22px;line-height:27px;letter-spacing:.8px}
.ci-item{position:absolute;left:44px;display:flex;align-items:center;gap:11px;font-size:11.5px}
.ci-icon{width:32px;height:32px;border:1.5px solid var(--white);border-radius:50%;display:flex;align-items:center;justify-content:center;flex:none}
.ci-name{font-weight:600;font-size:13px}
.social-row{position:absolute;left:46px;top:292px;display:flex;gap:17px}
.field{position:absolute;background:var(--white);color:#333;font-size:8.2px;padding:0 7px;display:flex;align-items:center}
.submit{position:absolute;left:370px;top:267px;width:150px;height:34px;background:var(--pink);color:var(--white);font-size:11px;letter-spacing:.8px;display:flex;align-items:center;justify-content:center}

.footer{left:0;top:1105px;width:722px;height:95px}
.fnav{left:46px;top:26px;display:flex;gap:22px;font-size:9px;letter-spacing:.4px}
.fnav .active{color:var(--red)}
.copy{left:46px;top:51px;font-size:7.8px;color:#444}
.member{left:542px;top:14px;font-size:9.5px;color:var(--red)}
.badge{left:527px;top:30px;width:150px;height:36px;background:#e6ecd9;border-radius:3px}
</style>
</head>
<body>

<div class="abs topbar">
  <div class="abs social"><i class="dot"></i><i class="dot"></i><i class="dot"></i><i class="dot"></i><i class="dot"></i></div>
  <div class="abs contact">
    <span><svg width="10" height="10" viewBox="0 0 24 24"><path fill="#fff" d="M6.6 10.8a15 15 0 0 0 6.6 6.6l2.2-2.2c.3-.3.7-.4 1-.2 1.1.4 2.3.6 3.6.6.6 0 1 .4 1 1V20c0 .6-.4 1-1 1A17 17 0 0 1 3 4c0-.6.4-1 1-1h3.5c.6 0 1 .4 1 1 0 1.3.2 2.5.6 3.6.1.3 0 .7-.2 1z"/></svg>0400 555 218</span>
    <span><svg width="11" height="9" viewBox="0 0 24 18"><rect width="24" height="18" rx="2" fill="#fff"/><path d="M1 2l11 8 11-8" stroke="#EC4F4E" stroke-width="2" fill="none"/></svg>rena@tidewaterbodywork.com.au</span>
  </div>
</div>

<header class="abs header">
  <div class="abs brand">
    <span class="brand-mark"></span>
    <div class="brand-name serif">TIDEWATER<br>BODYWORK</div>
  </div>
  <nav class="abs nav serif">
    <span>HOME</span><span>REMEDIAL MASSAGE</span><span>ABOUT ME</span><span class="active">FEES</span><span>CONTACT</span>
  </nav>
</header>

<section class="abs hero" role="img" aria-label="Photo of a woman relaxing during a hot stone massage">
  <h1 class="serif">HOURS</h1>
</section>

<svg class="abs hex" viewBox="0 0 255 294" role="img" aria-label="Hexagon-framed photo of a client receiving a back massage">
  <polygon points="127.5,3 251,74 251,220 127.5,291 4,220 4,74" fill="#d9a88a" stroke="#EB3D1F" stroke-width="5"/>
</svg>

<section class="abs hours">
  <h2 class="serif">OPENING HOURS</h2>
  <p>Sed ut perspiciatis unde omnis iste natus error sit voluptatem accusantium doloremque laudantium.</p>
  <table>
    <tr><td>MONDAY</td><td>10AM - 7PM</td></tr>
    <tr><td>TUESDAY</td><td>10AM - 7PM</td></tr>
    <tr><td>WEDNESDAY</td><td>10AM - 7PM</td></tr>
    <tr><td>THURSDAY</td><td>10AM - 7PM</td></tr>
    <tr><td>THURSDAY</td><td>10AM - 7PM</td></tr>
    <tr><td>SATURDAY</td><td>10AM - 5PM</td></tr>
    <tr><td>SUNDAY</td><td class="closed">CLOSED</td></tr>
  </table>
</section>

<section class="abs contact-band" role="img" aria-label="Red-tinted background photo of a massage session">
  <h2 class="serif" style="left:46px;top:48px">CONTACT<br>INFORMATION</h2>
  <h2 class="serif" style="left:370px;top:48px">QUICK<br>CONTACT FORM</h2>

  <div class="ci-item" style="top:124px">
    <span class="ci-icon"><svg width="14" height="12" viewBox="0 0 24 20"><path fill="#fff" d="M0 3l7-3 10 3 7-3v17l-7 3-10-3-7 3z"/></svg></span>
    <div><div class="ci-name">Rena Holt</div><div>24 Ferncliff Road Sandbay VIC 3199</div></div>
  </div>
  <div class="ci-item" style="top:175px">
    <span class="ci-icon"><svg width="12" height="12" viewBox="0 0 24 24"><path fill="#fff" d="M6.6 10.8a15 15 0 0 0 6.6 6.6l2.2-2.2c.3-.3.7-.4 1-.2 1.1.4 2.3.6 3.6.6.6 0 1 .4 1 1V20c0 .6-.4 1-1 1A17 17 0 0 1 3 4c0-.6.4-1 1-1h3.5c.6 0 1 .4 1 1 0 1.3.2 2.5.6 3.6.1.3 0 .7-.2 1z"/></svg></span>
    <div>0400 555 218</div>
  </div>
  <div class="ci-item" style="top:226px">
    <span class="ci-icon"><svg width="13" height="10" viewBox="0 0 24 18"><rect width="24" height="18" rx="2" fill="#fff"/><path d="M1 2l11 8 11-8" stroke="#c82d1a" stroke-width="2" fill="none"/></svg></span>
    <div>rena@tidewaterbodywork.com.au</div>
  </div>
  <div class="social-row"><i class="dot"></i><i class="dot"></i><i class="dot"></i><i class="dot"></i><i class="dot"></i></div>

  <div class="field" style="left:370px;top:114px;width:150px;height:34px">Name</div>
  <div class="field" style="left:528px;top:114px;width:150px;height:34px">Email Address</div>
  <div class="field" style="left:370px;top:157px;width:150px;height:34px">Phone No</div>
  <div class="field" style="left:528px;top:157px;width:150px;height:34px;justify-content:space-between">Select Date
    <svg width="8" height="8" viewBox="0 0 10 10"><rect x=".5" y="1.5" width="9" height="8" fill="none" stroke="#333"/><path d="M.5 3.5h9" stroke="#333"/></svg></div>
  <div class="field" style="left:370px;top:200px;width:308px;height:59px;align-items:flex-start;padding-top:11px">Message</div>
  <div class="submit serif">SUBMIT</div>
</section>

<footer class="abs footer">
  <nav class="abs fnav serif"><span class="active">HOME</span><span>REMEDIAL MASSAGE</span><span>ABOUT ME</span><span>FEES</span><span>CONTACT</span></nav>
  <div class="abs copy">Copyright© 2022 Company Name &nbsp;All Right Reserved</div>
  <div class="abs member">Member</div>
  <div class="abs badge" aria-label="Professional association member badge"></div>
</footer>

</body>
</html>
```